Kestrel Facilities Business Card Design

We would now like to design business cards with the new Kestrel Facilities logo

Target Market(s)

Professional

Industry/Entity Type

Professional services

Contact Information for Business Card

Employee name, title, phone number, email address, corporate office address and logo.

Font styles to use
Sans Serif

Colors
0054AA
0677BA
7BADD7
CADEEF
E8F1F8

Requirements
Must have
• My logo
Should not have
• any other pictures or images besides my logo

```html
<!DOCTYPE html>
<html lang="en">
<head>
<meta charset="utf-8">
<title>Kestrel Facilities Business Card</title>
<link href="https://fonts.googleapis.com/css2?family=Montserrat:wght@400;500;700&display=swap" rel="stylesheet">
<style>
  :root {
    --stage: #2c2c2e;
    --brand-blue: #3474bc;
    --band-grey: #a4a4a7;
    --card-white: #ffffff;
    --mark-silver: #d3d9e4;
    --text-light: #ffffff;
  }
  * { box-sizing: border-box; margin: 0; padding: 0; }
  html, body {
    width: 1200px; height: 960px; overflow: hidden;
    background: var(--stage);
    font-family: "Montserrat", sans-serif;
  }
  .stage {
    position: relative; width: 1200px; height: 960px;
    display: flex; flex-direction: column; align-items: center; justify-content: center; gap: 40px;
  }
  .card {
    position: relative; width: 700px; height: 400px;
    border-radius: 26px; overflow: hidden;
    box-shadow: 0 14px 30px rgba(0,0,0,0.45);
  }
  .card-back { background: var(--brand-blue); display: flex; align-items: center; justify-content: center; }
  .brand-lockup { display: flex; align-items: center; gap: 16px; }
  .brand-square { width: 34px; height: 34px; }
  .brand-name { font-weight: 700; letter-spacing: 0.5px; }
  .card-back .brand-square { background: var(--mark-silver); }
  .card-back .brand-name { color: var(--mark-silver); font-size: 40px; }

  .card-front { background: var(--card-white); }
  .front-wave { position: absolute; inset: 0; width: 700px; height: 400px; }
  .card-front .brand-lockup { position: absolute; top: 54px; right: 48px; }
  .card-front .brand-square { width: 26px; height: 26px; background: var(--brand-blue); }
  .card-front .brand-name { color: var(--brand-blue); font-size: 30px; }

  .contact { position: absolute; left: 52px; top: 222px; color: var(--text-light); }
  .contact-name { font-size: 25px; font-weight: 700; letter-spacing: 0.5px; }
  .contact-title { font-size: 18px; margin-top: 2px; }
  .contact-address { font-size: 16px; line-height: 21px; margin-top: 12px; }
  .contact-line { display: flex; align-items: center; gap: 8px; font-size: 16px; line-height: 23px; }
  .contact-lines { margin-top: 10px; }
  .contact-line svg { width: 16px; height: 16px; fill: var(--text-light); }
</style>
</head>
<body>
<main class="stage">
  <section class="card card-back">
    <div class="brand-lockup">
      <span class="brand-square"></span>
      <span class="brand-name">Kestrel Facilities</span>
    </div>
  </section>

  <section class="card card-front">
    <svg class="front-wave" viewBox="0 0 700 400" aria-hidden="true">
      <path d="M0,200 C140,150 280,140 400,152 C540,166 640,160 700,70" fill="none" stroke="var(--band-grey)" stroke-width="14"/>
      <path d="M0,222 C130,176 260,162 380,176 C520,192 630,186 700,100 L700,400 L0,400 Z" fill="var(--brand-blue)"/>
    </svg>
    <div class="brand-lockup">
      <span class="brand-square"></span>
      <span class="brand-name">Kestrel Facilities</span>
    </div>
    <div class="contact">
      <p class="contact-name">DANA WHITLOW</p>
      <p class="contact-title">Co-Founder</p>
      <p class="contact-address">4180 N. Harbor Lane<br>Suite 210 Fairhollow 14</p>
      <div class="contact-lines">
        <p class="contact-line">
          <svg viewBox="0 0 24 24"><path d="M6.6 10.8a15.1 15.1 0 0 0 6.6 6.6l2.2-2.2a1 1 0 0 1 1-.25 11.4 11.4 0 0 0 3.6.57 1 1 0 0 1 1 1V20a1 1 0 0 1-1 1A17 17 0 0 1 3 4a1 1 0 0 1 1-1h3.5a1 1 0 0 1 1 1c0 1.25.2 2.45.57 3.6a1 1 0 0 1-.25 1z"/></svg>
          +254-160-47213
        </p>
        <p class="contact-line">
          <svg viewBox="0 0 24 24"><path d="M2 5h20v14H2z M3.5 6.5 12 13l8.5-6.5" fill="none" stroke="#fff" stroke-width="2"/></svg>
          info@kestrelfacilities.com
        </p>
      </div>
    </div>
  </section>
</main>
</body>
</html>
```